Veriplume Digital Badge Header/Banner for Quillstep People Certificaiton

We need a new page header/banner for Veriplume https://www.badgequill.example/ where we have all our digital badges and certificates for our Nimbleway People Coaching https://www.badgequill.example/issuer/48213/credentials

https://www.badgequill.example/group/503118
https://www.badgequill.example/group/514927
https://www.badgequill.example/group/520364

https://www.brightfernpartners.example/

Target Market(s)

HR Professionals

Font styles to use
Sans Serif

```html
<!DOCTYPE html>
<html lang="en">
<head>
<meta charset="utf-8">
<title>Quillstep People – Digital Badges &amp; Certificates</title>
<link rel="stylesheet" href="https://fonts.googleapis.com/css2?family=Montserrat:wght@300&family=Poppins:wght@700;800&display=swap">
<style>
  :root {
    --page-bg: #ffffff;
    --banner-blue: #3d5fd6;
    --banner-indigo: #4a4fc4;
    --banner-violet: #7a4fd6;
    --accent-cyan: #00f3ff;
    --text-white: #ffffff;
  }
  html, body {
    margin: 0;
    padding: 0;
    width: 1200px;
    height: 511px;
    overflow: hidden;
    background: var(--page-bg);
  }
  .canvas {
    position: relative;
    width: 1200px;
    height: 511px;
    background: var(--page-bg);
  }
  .banner {
    position: absolute;
    left: 24px;
    top: 79px;
    width: 1152px;
    height: 351px;
    overflow: hidden;
  }
  .banner__artwork {
    position: absolute;
    inset: 0;
    background:
      radial-gradient(ellipse 60% 35% at 50% 52%, rgba(40, 30, 120, 0.35), transparent 70%),
      linear-gradient(100deg, var(--banner-blue) 0%, var(--banner-indigo) 50%, var(--banner-violet) 100%);
  }
  .banner__headline {
    position: absolute;
    inset: 0;
    margin: 0;
    text-align: center;
    font-weight: normal;
  }
  .headline__intro {
    position: absolute;
    left: 0;
    right: 0;
    top: 84px;
    font-family: "Montserrat", sans-serif;
    font-weight: 300;
    font-size: 44px;
    line-height: 1;
    letter-spacing: 2px;
    color: var(--text-white);
  }
  .headline__focus {
    position: absolute;
    left: 0;
    right: 0;
    top: 132px;
    font-family: "Poppins", sans-serif;
    font-weight: 800;
    font-size: 68px;
    line-height: 1;
    letter-spacing: -0.6px;
    color: var(--accent-cyan);
    white-space: nowrap;
  }
  .headline__program {
    position: absolute;
    left: 0;
    right: 0;
    top: 203px;
    font-family: "Poppins", sans-serif;
    font-weight: 800;
    font-size: 73px;
    line-height: 1;
    letter-spacing: -1.5px;
    color: var(--text-white);
    white-space: nowrap;
  }
</style>
</head>
<body>
  <div class="canvas">
    <header class="banner">
      <div class="banner__artwork" role="img" aria-label="Faint collage of digital badges and certificates of completion over a blue-to-violet gradient with a glowing network of connected lines"></div>
      <h1 class="banner__headline">
        <span class="headline__intro">WE HAVE ALL OUR</span>
        <span class="headline__focus">DIGITAL BADGES &amp; CERTIFICATES</span>
        <span class="headline__program">OUR QUILLSTEP PEOPLE</span>
      </h1>
    </header>
  </div>
</body>
</html>
```